Brekwell Automotive needs a catchy banner design

We need a design for a banner to be displayed on the fence in the outfield of a baseball stadium to show off our company and have people interested in what we do. We need something catchy that's going to attract people to look over at our banner.
We are a
Complete Automotive Service Company
Tires - Service - Repair - Diesel
We are in a Town called Ashford-Linden
(555)314-2609 we would like the phone number to be a descent size so when you are in the stands you can read it.
I have attached what we came up with but like I said we need it to pop more and make the viewer that's looking at it want to look us up.
The Banner size is 24ft long and 10ft tall

```html
<!DOCTYPE html>
<html lang="en">
<head>
<meta charset="utf-8">
<title>Brekwell Automotive – Outfield Banner</title>
<link rel="stylesheet" href="https://fonts.googleapis.com/css2?family=Montserrat:wght@500;700;800;900&display=swap">
<style>
  :root{
    --navy:#0a3d99;
    --royal:#1f56b0;
    --sky:#a6bedf;
    --bright:#1a8cf0;
    --cyan:#1ba0f5;
    --ink:#1b1b1b;
    --white:#ffffff;
    --title-top:#6fc6ff;
    --title-bottom:#0d4fc4;
  }
  *{margin:0;padding:0;box-sizing:border-box}
  html,body{width:1200px;height:500px;overflow:hidden;background:var(--navy)}
  .banner{position:relative;width:1200px;height:500px;overflow:hidden;font-family:"Montserrat",sans-serif}
  .banner-shapes,.banner-title{position:absolute;left:0;top:0}
  .title-line{font-family:"Montserrat",sans-serif;font-weight:900;font-size:60px;fill:url(#titleFill);stroke:var(--white);stroke-width:5px;paint-order:stroke;stroke-linejoin:round}
  .services{font-family:"Montserrat",sans-serif;font-weight:900;font-size:34px;fill:var(--white)}
  .contact{position:absolute;left:104px;top:375px;color:var(--white)}
  .contact-label{font-weight:900;font-size:19px;letter-spacing:.3px}
  .contact-phone{font-weight:800;font-size:35px;line-height:1.05;letter-spacing:-.5px}
  .contact-town{font-weight:500;font-size:28px;margin-top:12px;letter-spacing:.5px}
  .brand-name{position:absolute;left:470px;top:390px;width:200px;text-align:center;color:var(--navy);font-weight:800;font-size:26px;line-height:1.1}
</style>
</head>
<body>
<div class="banner">
  <svg class="banner-shapes" width="1200" height="500" viewBox="0 0 1200 500">
    <defs>
      <linearGradient id="skyFill" x1="0" y1="0" x2="0" y2="1">
        <stop offset="0" stop-color="#0b3a97"/>
        <stop offset=".45" stop-color="#1f56b0"/>
        <stop offset=".8" stop-color="#a6bedf"/>
      </linearGradient>
      <linearGradient id="workshopFill" x1="0" y1="0" x2="1" y2="1">
        <stop offset="0" stop-color="#14213a"/>
        <stop offset=".5" stop-color="#2c3e5c"/>
        <stop offset="1" stop-color="#1c8fe0"/>
      </linearGradient>
    </defs>
    <rect width="1200" height="500" fill="url(#skyFill)"/>
    <path d="M0 322 C60 270 120 235 170 233 C300 232 500 300 690 362 L690 500 L0 500 Z" fill="var(--ink)"/>
    <path d="M0 420 C80 350 200 300 320 298 C450 296 580 330 690 368 L690 500 L0 500 Z" fill="var(--bright)"/>
    <path d="M307 304 C450 304 580 334 690 372 L690 500 L526 500 Z" fill="var(--white)"/>
    <path d="M0 445 C90 370 200 305 307 302 L526 500 L0 500 Z" fill="var(--navy)"/>
    <path d="M913 0 L1200 0 L1200 500 L666 500 C680 300 760 120 913 0 Z" fill="var(--bright)"/>
    <path d="M1000 22 C1080 5 1160 5 1200 8 L1200 500 L680 500 C690 300 820 80 1000 22 Z" fill="var(--ink)"/>
    <path d="M1200 28 L1200 500 L690 500 C700 310 820 100 1000 50 C1080 30 1150 28 1200 28 Z" fill="var(--cyan)"/>
    <path role="img" aria-label="Photo of a mechanic in a grey and red work uniform fitting a brake disc on a lifted vehicle" d="M1200 70 L1200 500 L700 500 C710 330 800 150 960 80 C1040 65 1130 66 1200 70 Z" fill="url(#workshopFill)"/>
  </svg>

  <svg class="banner-title" width="760" height="210" viewBox="0 0 760 210">
    <defs>
      <linearGradient id="titleFill" x1="0" y1="0" x2="0" y2="1">
        <stop offset="0" stop-color="var(--title-top)"/>
        <stop offset="1" stop-color="var(--title-bottom)"/>
      </linearGradient>
    </defs>
    <text class="title-line" x="214" y="87" textLength="320" lengthAdjust="spacingAndGlyphs">COMPLETE</text>
    <text class="title-line" x="35" y="148" textLength="678" lengthAdjust="spacingAndGlyphs">AUTOMOTIVE SERVICE</text>
    <text class="services" x="89" y="195" textLength="570" lengthAdjust="spacingAndGlyphs">TIRES - SERVICE - REPAIR - DIESEL</text>
  </svg>

  <div class="contact">
    <p class="contact-label">CALL US:</p>
    <p class="contact-phone">(555)314-2609</p>
    <p class="contact-town">Ashford-Linden</p>
  </div>

  <p class="brand-name">Brekwell Automotive</p>
</div>
</body>
</html>
```